Brightfen Business Card Redesign & Logo Update

We need to update our business cards to something more modern and fresh. Brightfen can provide the current color schemes and old design examples, but welcome creativity in helping us with this redesign. PLEASE NOTE that we no longer utilize the "tree" and/or "leaf" imagery in our branding. If able would apprecaite an update on the quality of our "words only" logo in Ai. / PNG formats too.

Target Market(s)

Investors, landowners, corporate partners, contractors

Industry/Entity Type

Environmental Restoration & Conservation

Contact Information for Business Card

Logo, persons name, title, mailing address, phone and email, website url

Font styles to use
Other font styles liked:
• Merriweather

Requirements
Nice to have
• Logo, persons name, title, mailing address, phone and email, website url, but open to ideams
Should not have
• No all back backgrounds

```html
<!DOCTYPE html>
<html lang="en">
<head>
<meta charset="UTF-8">
<title>Brightfen Business Card</title>
<link rel="stylesheet" href="https://fonts.googleapis.com/css2?family=Oswald:wght@400;500&family=Source+Sans+3:wght@400;600;700&display=swap">
<style>
  :root {
    --backdrop: #e4e4e4;
    --card-deep: #1d4a33;
    --card-light: #f4f4f4;
    --brand-orange: #e77a23;
    --brand-green: #157a3c;
    --brand-leaf: #7cc493;
    --ink: #2b2b2b;
    --paper-white: #ffffff;
  }
  * { margin: 0; padding: 0; box-sizing: border-box; }
  html, body {
    width: 1200px;
    height: 960px;
    overflow: hidden;
    background: var(--backdrop);
  }
  .stage { position: relative; width: 1200px; height: 960px; }

  .card {
    position: absolute;
    left: 297px;
    width: 609px;
    height: 348px;
  }
  .card--front { top: 109px; background: var(--card-deep); }
  .card--back { top: 511px; background: var(--card-light); }

  .wordmark {
    font-family: "Oswald", sans-serif;
    font-weight: 500;
    color: var(--brand-orange);
    text-transform: uppercase;
    letter-spacing: 0.04em;
    line-height: 1;
    display: flex;
    align-items: center;
  }
  .wordmark__dot {
    display: inline-block;
    background: var(--brand-green);
    border-radius: 50%;
  }
  .tagline {
    font-family: "Oswald", sans-serif;
    font-weight: 400;
    text-transform: uppercase;
    white-space: nowrap;
    line-height: 1;
  }

  .front-logo {
    position: absolute;
    left: 0; right: 0;
    top: 120px;
    display: flex;
    flex-direction: column;
    align-items: center;
  }
  .front-logo .wordmark { font-size: 58px; gap: 10px; }
  .front-logo .wordmark__dot { width: 15px; height: 15px; background: var(--brand-leaf); }
  .front-logo .tagline {
    margin-top: 68px;
    font-size: 18px;
    color: var(--paper-white);
    letter-spacing: 0.01em;
  }

  .back-logo {
    position: absolute;
    left: 50px;
    top: 72px;
  }
  .back-logo .wordmark { font-size: 40px; gap: 8px; }
  .back-logo .wordmark__dot { width: 11px; height: 11px; }
  .back-logo .tagline {
    margin-top: 44px;
    font-size: 12.5px;
    color: var(--ink);
    font-weight: 500;
  }

  .person {
    position: absolute;
    right: 47px;
    top: 150px;
    text-align: right;
    font-family: "Source Sans 3", sans-serif;
  }
  .person__name {
    font-size: 20px;
    font-weight: 700;
    color: var(--brand-orange);
    line-height: 1.2;
  }
  .person__title {
    font-size: 15px;
    color: var(--ink);
    line-height: 1.3;
  }

  .contact {
    position: absolute;
    left: 49px;
    top: 206px;
    list-style: none;
    font-family: "Source Sans 3", sans-serif;
    font-size: 15.5px;
    color: var(--ink);
    line-height: 20px;
  }
  .contact__item {
    display: flex;
    align-items: flex-start;
    gap: 6px;
  }
  .contact__item--address { margin-bottom: 6px; }
  .contact__icon {
    width: 14px;
    height: 14px;
    margin-top: 3px;
    flex: none;
    fill: none;
    stroke: var(--brand-orange);
    stroke-width: 1.8;
    stroke-linecap: round;
    stroke-linejoin: round;
  }
</style>
</head>
<body>
<main class="stage">

  <section class="card card--front" aria-label="Card front">
    <div class="front-logo">
      <div class="wordmark">Brightfen<span class="wordmark__dot"></span></div>
      <p class="tagline">Environmental Credit Company</p>
    </div>
  </section>

  <section class="card card--back" aria-label="Card back">
    <div class="back-logo">
      <div class="wordmark">Brightfen<span class="wordmark__dot"></span></div>
      <p class="tagline">Environmental Credit Company</p>
    </div>

    <div class="person">
      <p class="person__name">Daniel Porter</p>
      <p class="person__title">Owner</p>
    </div>

    <ul class="contact">
      <li class="contact__item contact__item--address">
        <svg class="contact__icon" viewBox="0 0 16 16" aria-hidden="true">
          <path d="M8 15s5-5 5-8.5A5 5 0 0 0 3 6.5C3 10 8 15 8 15z"/>
          <circle cx="8" cy="6.5" r="1.8"/>
        </svg>
        <span>418 Meadow Lane, Suite 210<br>Fairhaven, CA 95012</span>
      </li>
      <li class="contact__item">
        <svg class="contact__icon" viewBox="0 0 16 16" aria-hidden="true">
          <path d="M4.5 1.5l2 3-1.5 1.5a8 8 0 0 0 5 5l1.5-1.5 3 2-1.5 2.5C7 14 2 9 2 3z"/>
        </svg>
        <span>530-555-0142</span>
      </li>
      <li class="contact__item">
        <svg class="contact__icon" viewBox="0 0 16 16" aria-hidden="true">
          <rect x="1.5" y="3" width="13" height="10" rx="1"/>
          <path d="M1.5 4l6.5 5 6.5-5"/>
        </svg>
        <span>daniel@brightfen.com</span>
      </li>
      <li class="contact__item">
        <svg class="contact__icon" viewBox="0 0 16 16" aria-hidden="true">
          <circle cx="8" cy="8" r="6.5"/>
          <path d="M1.5 8h13M8 1.5c-3 3.5-3 9.5 0 13M8 1.5c3 3.5 3 9.5 0 13"/>
        </svg>
        <span>www.brightfen.com</span>
      </li>
    </ul>
  </section>

</main>
</body>
</html>
```